Geschäftspapiere für Jobwebseite
Zielgruppe
Hier finden sie alle Informationen zu unserem Unternehmen:
https://www.sauberwerk-stelle.com
Aufgabenstellung
Gerne von den Farben angelehnt an die Website ein modernes Briefpapier gestalten.

```html
<!DOCTYPE html>
<html lang="de">
<head>
<meta charset="utf-8">
<title>Briefpapier – Sauberwerk-Stelle</title>
<link href="https://fonts.googleapis.com/css2?family=PT+Sans:wght@400;700&display=swap" rel="stylesheet">
<style>
  :root {
    --backdrop: #2c2c2c;
    --paper: #ffffff;
    --ink: #2e2e2e;
    --brand-dark: #2a2f36;
    --brand-green: #0a8a3c;
    --signature-tone: #d9dcef;
  }
  html, body {
    margin: 0;
    padding: 0;
    width: 1200px;
    height: 798px;
    overflow: hidden;
    background: var(--backdrop);
    font-family: "PT Sans", sans-serif;
    color: var(--ink);
  }
  .letterhead {
    position: absolute;
    left: 331px;
    top: 19px;
    width: 537px;
    height: 760px;
    background: var(--paper);
  }
  .brand {
    position: absolute;
    left: 51px;
    top: 36px;
    display: flex;
    align-items: center;
    gap: 5px;
    font-weight: 700;
    font-size: 14px;
    letter-spacing: 0.2px;
    color: var(--brand-dark);
  }
  .brand-dot {
    width: 7px;
    height: 7px;
    background: var(--brand-green);
  }
  .sender {
    position: absolute;
    left: 51px;
    top: 255px;
    width: 110px;
    font-size: 6.2px;
    line-height: 9.3px;
  }
  .sender p { margin: 0 0 9.3px; }
  .sender-name { color: var(--brand-green); font-weight: 700; }
  .sender b { font-weight: 700; margin-right: 2px; }
  .letter-body {
    position: absolute;
    left: 171px;
    top: 253px;
    width: 334px;
    font-size: 8.2px;
    line-height: 10.9px;
  }
  .letter-body p { margin: 0 0 10.9px; }
  .salutation { margin-bottom: 21.8px !important; }
  .signature {
    width: 110px;
    height: 28px;
    background: linear-gradient(90deg, var(--signature-tone), #eef0f8);
    margin: 0 0 -4px;
  }
  .signer { margin: 0; }
  .web-band {
    position: absolute;
    left: 0;
    top: 715px;
    width: 151px;
    height: 17px;
    background: var(--brand-green);
    color: var(--paper);
    font-size: 6.4px;
    font-weight: 700;
    line-height: 17px;
    padding-left: 51px;
    box-sizing: border-box;
    letter-spacing: 0.2px;
  }
</style>
</head>
<body>
  <main class="letterhead">
    <div class="brand"><span class="brand-name">SAUBERWERK-STELLE.de</span><span class="brand-dot"></span></div>

    <aside class="sender">
      <p><span class="sender-name">sauberwerk-stelle.de</span><br>Lindenhof 12<br>74078 Talheim</p>
      <p><b>M</b>info@sauberwerk-stelle.de<br><b>T</b> 07131 555 012 3</p>
      <p>Inhaber<br>Herr Lukas Bernau</p>
      <p>Amtsgericht Talheim<br>HRB xxxx<br>USt-IdNr. DExxxxxxx</p>
    </aside>

    <section class="letter-body">
      <p class="salutation">Sehr geehrter Herr Mustermann,</p>
      <p>Ferem sit, omniendaecte doluptature mo cuptatio. Ebitati ssumqui coria poreici destrum, vidusap elibus qui ipideli tatecabo. Et remporporio di quo ommolup taessit, ius non esequibus et volupiditio optatur ereicat laut et et quae ium int ma sum cori omnimin recus, ent molupti orrores truptassin eos a cor sa sus dolupta sitist laut que plignat.<br>Axim exeribus. Pudit arum ium ipiet in ni od mos ent liciam quunt aborporem verferr uptasim ra de int quunt a inimin et il mi, eaque volo bla volo bea qui ius, sum volo Ibus, acepernatem aut explabo rporupta pa qui consediam atus.</p>
      <p>Aximporporum et dolore conecerferia venimet verae sum nobist asintorest, eosant alique volut qui te nullo eum que velitatatis iumque mint ut volupta tquiatemodi dolless itature, et laccuptae pa invelis sequunt, velique abo. Obis sus et officipsamus premquidi blabo. Dollore rnatend untiatu reperion consequam faccaborit faciates sitatenet harunt invenim di sumque.</p>
      <p>Pore oditam identitiis dit estrunt officta tecust pro maionsequis del mos aut quiatur? Icillab ipsapie nihilluptas mo et que sitatiis dolupta quament laborro cuptae. Namus, utendunt.Pictat. Otae nimet faccatur? Erumqui at occum ratquia nos viti con reiunt volorro ommodit, nusam ratiasr itatet pa quistionsed explitem. Nam inis essinve litatib usdandit miliaspedi aces utatem facia volesci alit evel iuntis unt ab ilit autem quam archilluptae</p>
      <p>Sit laut qui tem rerum as reperae porempedi neces et acculparum fugiae denetur, torernam verepti issinullenis arum re dolessi sum rerum ra di que vel minciam duntio. Aborios molutae praest, corit quiaerci sus andigente sincius si occum fugiae reperibus delicab is sunt magnam is vento to blandiscia quo dolorro vitasped evelest, suntemp oreictor a porepudaeri que conem aut mint alitam si quae volorro rerferia volorepeliti ad ma voluptat acest estrupta si voloriscid millatatae re, offictis aperor maio. Ut liquam erum eum dunt offici dolenih ilibus, id erro et volupta volectent que pla sitis exped maio. Nam sitatur sit qui comnima ximpore consect ibeatatum aut in nulparc hilite nonsequia autemquat.</p>
      <p>Mit freundlichen Grüßen</p>
      <div class="signature" role="img" aria-label="Handschriftliche Unterschrift"></div>
      <p class="signer">Max Mustermann</p>
    </section>

    <div class="web-band">WWW.SAUBERWERK-STELLE.DE</div>
  </main>
</body>
</html>
```